Cruise Booking Website

Cruise search and booking website

This project is a redesign of a cruise booking website we did a few years ago.

The current website is located here: http://voyage.pylonworks.example/en/

It's not fully functional but gives you ad idea how miserable the old design was.

All the information about cruises, cruise lines, destinations, ports and shore excursions will be similar to http://www.sailquest.example/
Actual search pages (form, results, single result, sailing and cabin selection, ship info, booking) will have EXACTLY the same info as sailquest.example

We like the style of http://harborfleetdesk.example, it's quite modern, good spacing, not overloaded with information. So you can use it as an example of what we like, not what we want as a final result for us. Please, don't copy it. The result should not be possible to resemble the harborfleetdesk.example, because our site has to be unique. This is important!
If you submit a design that clearly reminds another cruise site it will be rejected!

Also the mockup provided is just to give you the basic structure and show what information has to be present on the page. It doesn't mean the layout has to be the same as a mockup. The layout is up to the designer.

I've updated the mockup to be more generic so it doesn't confuse you:
https://files.boxvault.example/s/k7m2qp9wz4hx/Home%20page.png

When you're adding social sharing icons like plazanet/chirpline you have to use chinese ones instead:
https://files.boxvault.example/s/t3nr8vx5lc2e/chinese-social-icons.png
Originals: http://minilk.example/qR7t

We'll start with home page first and after it's approved inner pages can be designed.

I know the cost of the project doesn't look high, but the task is straight forward and doesn't require to be very original, it's better to follow existing design and layout patterns that proved to work well.
That's why I encourage you to choose a template to build the design on top of one of https://themeparlor.example/ themes if it will save the design work, will be easier and faster for you. So it will be more like a customization than a new design from scratch.

Mockups, site map and logo files:
- https://files.boxvault.example/sh/h48dm2rs73fkpw/QvnbW2Xz8e

Website tree:
- https://sheets.papernest.example/document/d/7xPqR2mLw9sTk4VbN8cHj3YzA6eUf5GdKo1iMnBv/edit?usp=sharing
Updates

So far a lot of designs are just copying http://www.harborfleetdesk.example/ - we don't like it!

We like the style of harborfleetdesk.example, it's quite modern, good spacing, not overloaded with information. So you can use it as an example of what we like, not what we want as a final result for us. Please, don't copy it. The result should not be possible to resemble the harborfleetdesk.example, because our site has to be unique. This is important!

Target Market(s)

Chinese travellers

Industry/Entity Type

Build

Requirements
Must have
• * White, blue and red
* Large spacing, not too much information cramped into a small space like sailquest.example or the current website
* More "hidden" info in popups, tabs and so on, so not to many things are visible at the same time
* Compatible with kestrel scaffold styling (for easier coding):
- http://kestrelkit.codeshelf.example/scaffold/index.html
- http://skinmarket.example/
* Feel free to propose to build the design on top of one of https://themeparlor.example/ themes if it will save the design work, will be easier and faster for you

```html
<!DOCTYPE html>
<html lang="en">
<head>
<meta charset="utf-8">
<title>Haiyun Cruise – Sign in / Sign up</title>
<link href="https://fonts.googleapis.com/css2?family=Source+Sans+3:wght@400;600;700&display=swap" rel="stylesheet">
<style>
:root{
  --blue:#1f6aa8;
  --blue-dark:#0c5a96;
  --nav-top:#1b7cc6;
  --nav-bottom:#0b5c9e;
  --nav-active:#35a3e6;
  --orange-top:#ffa12a;
  --orange-bottom:#f26c06;
  --footer:#4a7fae;
  --footer-bottom:#3c6f9e;
  --page-edge:#2b6ea8;
  --page-mid:#cfe2f1;
  --field-border:#b9c2ca;
  --panel-border:#e4e7ea;
  --text-light:#ffffff;
  --label:#1f6aa8;
  --grey:#6d7378;
}
*{box-sizing:border-box;margin:0;padding:0}
html,body{width:1200px;height:899px;overflow:hidden}
body{
  font-family:"Source Sans 3",sans-serif;
  background:radial-gradient(ellipse 60% 80% at 50% 45%,var(--page-mid) 0%,#8fbbe0 45%,var(--page-edge) 100%);
  position:relative;
}
.site{position:absolute;left:180px;top:0;width:840px;height:899px;background:#fff}
.abs{position:absolute}

/* header */
.brand{left:10px;top:34px;display:flex;align-items:center;gap:10px}
.brand-mark{width:46px;height:46px;border-radius:50%;background:var(--blue)}
.brand-name{font-size:28px;font-weight:700;color:var(--blue);line-height:1}
.brand-url{font-size:11px;font-weight:700;color:var(--blue);letter-spacing:.3px;margin-top:3px}
.account{left:614px;top:16px;font-size:12px;color:var(--blue)}
.account span{margin:0 8px}
.social{left:722px;top:13px;display:flex;gap:3px}
.social i{display:block;width:24px;height:24px;border-radius:4px}
.social i:nth-child(1){background:#e8312f}
.social i:nth-child(2){background:#2aa6de}
.social i:nth-child(3){background:#f4a10b}
.social i:nth-child(4){background:#d9262b}
.phone{left:454px;top:51px;display:flex;gap:8px}
.phone-number{font-size:21px;font-weight:700;color:var(--blue);line-height:1;margin-top:0}
.phone-tag{font-size:15px;color:#333;line-height:1.2}
.search{left:626px;top:65px;width:198px;height:22px;border:1px solid var(--field-border);border-radius:2px;background:linear-gradient(#f3f3f3,#fff);font-size:8px;color:var(--grey);padding:6px 10px}
.search svg{position:absolute;right:7px;top:4px}

/* nav */
.nav{left:0;top:111px;width:840px;height:35px;background:linear-gradient(var(--nav-top),var(--nav-bottom));display:flex}
.nav a{height:35px;line-height:35px;color:#fff;font-size:11px;font-weight:700;text-decoration:none;text-align:center;border-right:1px solid rgba(255,255,255,.18)}
.nav a.active{background:linear-gradient(#4db4f0,var(--nav-active))}
.nav a:last-child{border-right:0}

.crumbs{left:20px;top:165px;font-size:11px;color:var(--blue)}
.crumbs b{font-weight:400;color:#999;margin:0 6px}

/* forms */
.form-title{font-size:17px;font-weight:700;color:var(--blue)}
.panel{border:1px solid var(--panel-border);background:linear-gradient(#f5f5f5,#fff 70%);border-radius:2px}
.label{font-size:9px;font-weight:600;color:var(--label)}
.field{width:263px;height:23px;border:1px solid var(--field-border);border-radius:2px;background:linear-gradient(#f1f1f1,#fff);font-size:8px;color:var(--grey);padding:7px 12px}
.btn{width:106px;height:30px;border-radius:2px;background:linear-gradient(var(--orange-top),var(--orange-bottom));color:#fff;font-size:11px;font-weight:600;text-align:center;line-height:30px}
.check{width:14px;height:14px;border:1px solid var(--field-border);border-radius:3px;background:#eef0f2}

/* partners */
.partners-title{left:15px;top:549px;font-size:16px;font-weight:700;color:var(--blue)}
.arrow{width:17px;height:17px;border:1px solid #ccc;background:#e9e9e9;top:551px}
.partner{top:581px;width:124px;height:63px;border:1px solid #d6d9dc;background:#fff;display:flex;align-items:center;justify-content:center}
.partner i{display:block;width:70px;height:22px;border-radius:11px;opacity:.85}

/* footer */
.footer{left:0;top:665px;width:840px;height:191px;background:var(--footer)}
.footer-bottom{left:0;top:856px;width:840px;height:43px;background:var(--footer-bottom);color:#fff;font-size:9px;text-align:center;line-height:43px}
.f-head{font-size:14px;font-weight:600;color:var(--text-light)}
.f-links{list-style:none;font-size:9px;color:#fff}
.f-links li{height:19px}
.about-logo{left:347px;top:63px;width:85px;height:84px;background:#fff;border:2px solid #dfe7ee;display:flex;flex-direction:column;align-items:center;justify-content:center;gap:4px}
.about-logo i{display:block;width:34px;height:34px;border-radius:50%;background:var(--blue)}
.about-logo span{font-size:10px;font-weight:700;color:var(--blue)}
.f-text{font-size:11px;color:#fff;line-height:15.5px}
.contact-line{display:flex;align-items:center;gap:6px;font-size:11px;color:#fff}
</style>
</head>
<body>
<div class="site">

  <header>
    <div class="abs brand">
      <span class="brand-mark"></span>
      <div>
        <div class="brand-name">Haiyun Cruise</div>
        <div class="brand-url">www.haiyunsail.example</div>
      </div>
    </div>
    <div class="abs account">Sign in<span>|</span>Signup</div>
    <div class="abs social" aria-label="Social networks"><i></i><i></i><i></i><i></i></div>
    <div class="abs phone">
      <svg width="32" height="32" viewBox="0 0 32 32" aria-hidden="true">
        <circle cx="16" cy="16" r="14.5" fill="#f4f4f4" stroke="#b8b8b8"/>
        <path d="M12 8c-2 1-3 3-2 7s4 8 7 9c2 1 4 0 5-1l-3-3-2 1c-2-1-4-4-4-6l1-2z" fill="none" stroke="#777" stroke-width="1.6"/>
      </svg>
      <div>
        <div class="phone-number">400 512 512</div>
        <div class="phone-tag">Call Us Today!</div>
      </div>
    </div>
    <div class="abs search">SEARCH :
      <svg width="13" height="13" viewBox="0 0 13 13" aria-hidden="true"><circle cx="5.5" cy="5.5" r="4" fill="none" stroke="#bbb" stroke-width="1.5"/><path d="M8.5 8.5l3.5 3.5" stroke="#bbb" stroke-width="1.5"/></svg>
    </div>
  </header>

  <nav class="abs nav">
    <a class="active" style="width:86px">HOME</a>
    <a style="width:121px">DESTINATIONS</a>
    <a style="width:110px">CRUISE LINES</a>
    <a style="width:108px">CRUISE INFO</a>
    <a style="width:81px">DEALS</a>
    <a style="width:132px">ONLINE BOOKING</a>
    <a style="width:107px">CONTACT US</a>
    <a style="width:95px">BLOG</a>
  </nav>

  <div class="abs crumbs">HOME<b>›</b>SIGNIN / SIGNUP</div>

  <!-- login -->
  <h2 class="abs form-title" style="left:97px;top:216px">LOGIN</h2>
  <section class="abs panel" style="left:82px;top:250px;width:304px;height:200px"></section>
  <div class="abs label" style="left:107px;top:263px">LOGIN</div>
  <div class="abs field" style="left:103px;top:283px">USERNAME OR EMAIL :</div>
  <div class="abs label" style="left:107px;top:318px">PASSWORD :</div>
  <div class="abs field" style="left:103px;top:338px">PASSWORD :</div>
  <div class="abs label" style="left:108px;top:378px">REMEMBER ME</div>
  <div class="abs check" style="left:172px;top:377px"></div>
  <div class="abs btn" style="left:103px;top:404px">LOGIN</div>

  <!-- register -->
  <h2 class="abs form-title" style="left:466px;top:216px">REGISTER</h2>
  <section class="abs panel" style="left:451px;top:250px;width:304px;height:277px"></section>
  <div class="abs label" style="left:476px;top:263px">LOGIN</div>
  <div class="abs field" style="left:471px;top:283px">USERNAME :</div>
  <div class="abs label" style="left:476px;top:318px">PASSWORD :</div>
  <div class="abs field" style="left:471px;top:338px">PASSWORD :</div>
  <div class="abs label" style="left:476px;top:373px">PASSWORD ( AGAIN ) :</div>
  <div class="abs field" style="left:471px;top:392px">PASSWORD :</div>
  <div class="abs label" style="left:476px;top:426px">EMAIL ( OPTIONAL ) :</div>
  <div class="abs field" style="left:471px;top:446px">EMAIL ID :</div>
  <div class="abs btn" style="left:471px;top:485px">REGISTER</div>

  <!-- partners -->
  <h2 class="abs partners-title">OUR RELIABLE PARTNERS</h2>
  <div class="abs arrow" style="left:786px"><svg width="15" height="15" viewBox="0 0 15 15" aria-hidden="true"><path d="M9 3.5L5 7.5l4 4" fill="none" stroke="#888" stroke-width="1.4"/></svg></div>
  <div class="abs arrow" style="left:806px"><svg width="15" height="15" viewBox="0 0 15 15" aria-hidden="true"><path d="M6 3.5l4 4-4 4" fill="none" stroke="#888" stroke-width="1.4"/></svg></div>
  <div class="abs partner" style="left:16px"><i style="background:#c9d6e8"></i></div>
  <div class="abs partner" style="left:153px"><i style="background:#c9d9ef"></i></div>
  <div class="abs partner" style="left:290px"><i style="background:#d3dde6"></i></div>
  <div class="abs partner" style="left:427px"><i style="background:#f6d9b3"></i></div>
  <div class="abs partner" style="left:564px"><i style="background:#cbe4f4"></i></div>
  <div class="abs partner" style="left:701px"><i style="background:#c6def4"></i></div>

  <!-- footer -->
  <footer>
    <div class="abs footer">
      <h3 class="abs f-head" style="left:27px;top:33px">Useful Pages</h3>
      <ul class="abs f-links" style="left:27px;top:58px">
        <li>About Us</li><li>Contact us</li><li>Blog</li><li>FAQ</li><li>Terms of Service</li><li>Payment info</li><li>Reward Points</li>
      </ul>
      <h3 class="abs f-head" style="left:190px;top:33px">Cruise Infov</h3>
      <ul class="abs f-links" style="left:192px;top:57px">
        <li>Cruise news</li><li>Visa</li><li>Honeymoon cruises</li><li>Firsttime on a Cruise</li>
      </ul>
      <h3 class="abs f-head" style="left:347px;top:38px">About haiyunsail.example</h3>
      <div class="abs about-logo"><i></i><span>Haiyun</span></div>
      <p class="abs f-text" style="left:449px;top:76px;width:110px">We're the most advanced cruise booking providr in china.</p>
      <h3 class="abs f-head" style="left:604px;top:38px">Contact Us</h3>
      <p class="abs f-text" style="left:605px;top:63px;line-height:16.5px;font-size:12px">Tidewater Studio Pte Ltd<br>Harbourview Block 18, Quay Road 3<br>Port Alder 20417 Marinea</p>
      <div class="abs contact-line" style="left:606px;top:121px">
        <svg width="13" height="10" viewBox="0 0 13 10" aria-hidden="true"><path d="M1 4c0-3 11-3 11 0l-2 1-1-2H4L3 5z M3 6h7l1 3H2z" fill="#fff"/></svg>
        (123) 555-0142 - (123) 555-0187
      </div>
      <div class="abs contact-line" style="left:606px;top:142px">
        <svg width="13" height="10" viewBox="0 0 13 10" aria-hidden="true"><rect x="0.5" y="0.5" width="12" height="9" fill="#fff"/><path d="M1 1l5.5 4.5L12 1" fill="none" stroke="#4a7fae"/></svg>
        hello@haiyunsail.example
      </div>
    </div>
    <div class="abs footer-bottom">© 2013. haiyunsail. All rights reserved.</div>
  </footer>

</div>
</body>
</html>
```